Local Roofing/Construction company business needs new biz card design

We need a new business card design, current cards are from the start of this operation and generic at best. We are a local Construction Company (General Contractor) with a majority of our work originating from insurance claims-exterior finish work is the main focus (Roofs-Siding-Gutters etc). Heavily involved with homeowners and the low ball offers they receive from insurance company's after a insurable event takes place. I have attached some of our original logo file(s) below.

```html
<!DOCTYPE html>
<html lang="en">
<head>
<meta charset="utf-8">
<title>Stonebay Construction – Business Card</title>
<link href="https://fonts.googleapis.com/css2?family=Montserrat:wght@400;500;700;800&display=swap" rel="stylesheet">
<style>
  :root {
    --canvas: #e7e8e6;
    --card-white: #f8f6f3;
    --deep-teal: #13242a;
    --brand-green: #55b96c;
    --ink: #1c1c1c;
  }
  * { box-sizing: border-box; margin: 0; padding: 0; }
  html, body {
    width: 1200px; height: 900px; overflow: hidden;
    background: var(--canvas);
    font-family: "Montserrat", Arial, sans-serif;
  }
  .stage { position: relative; width: 1200px; height: 900px; }
  .card {
    position: absolute; width: 560px; height: 320px;
    border-radius: 22px; overflow: hidden;
    background: var(--card-white);
    box-shadow: 0 14px 30px rgba(0,0,0,.18);
  }
  .card svg.card-art { position: absolute; inset: 0; }
  .card--front { left: 60px; top: 90px; }
  .card--back { left: 580px; top: 490px; }

  .wordmark {
    position: absolute; display: flex; align-items: center; gap: 12px;
  }
  .wordmark__square {
    width: 34px; height: 34px; border-radius: 4px; background: var(--brand-green);
  }
  .wordmark__name {
    font-weight: 800; color: var(--ink); text-transform: uppercase;
    line-height: 1.05; letter-spacing: .5px;
  }
  .card--front .wordmark { left: 250px; top: 118px; }
  .card--front .wordmark__name { font-size: 26px; }

  .card--back .wordmark { left: 34px; top: 120px; flex-direction: column; align-items: flex-start; gap: 10px; }
  .card--back .wordmark__square { width: 78px; height: 78px; border-radius: 14px; }
  .card--back .wordmark__name { font-size: 17px; color: var(--brand-green); }

  .contact { position: absolute; left: 300px; top: 36px; }
  .contact__name { font-size: 22px; font-weight: 700; color: var(--brand-green); }
  .contact__title {
    font-size: 12px; color: var(--ink); padding-bottom: 6px;
    border-bottom: 1px solid var(--ink); width: 150px; margin-top: 2px;
  }
  .contact__list { list-style: none; margin-top: 12px; }
  .contact__list li {
    display: flex; align-items: center; gap: 9px;
    font-size: 11.5px; color: var(--ink); margin-bottom: 5px;
  }
  .contact__list svg { width: 12px; height: 12px; fill: var(--brand-green); flex: none; }
  .social { display: flex; gap: 8px; margin-top: 12px; margin-left: 20px; }
  .social span { width: 13px; height: 13px; border-radius: 3px; background: var(--brand-green); }
</style>
</head>
<body>
<main class="stage">

  <section class="card card--front" aria-label="Card front">
    <svg class="card-art" width="560" height="320" viewBox="0 0 560 320">
      <rect width="560" height="320" fill="var(--deep-teal)"/>
      <circle cx="530" cy="0" r="384" fill="var(--brand-green)"/>
      <circle cx="530" cy="0" r="376" fill="var(--card-white)"/>
      <circle cx="530" cy="0" r="372" fill="var(--brand-green)"/>
      <circle cx="530" cy="0" r="366" fill="var(--card-white)"/>
    </svg>
    <div class="wordmark">
      <span class="wordmark__square"></span>
      <span class="wordmark__name">Stonebay<br>Construction</span>
    </div>
  </section>

  <section class="card card--back" aria-label="Card back">
    <svg class="card-art" width="560" height="320" viewBox="0 0 560 320">
      <path d="M0 278 Q330 250 560 110 L560 320 L0 320 Z" fill="var(--brand-green)"/>
      <path d="M0 284 Q330 258 560 118 L560 320 L0 320 Z" fill="var(--card-white)"/>
      <path d="M0 290 Q330 268 560 130 L560 320 L0 320 Z" fill="var(--deep-teal)"/>
    </svg>
    <div class="wordmark">
      <span class="wordmark__square"></span>
      <span class="wordmark__name">Stonebay<br>Construction</span>
    </div>
    <div class="contact">
      <h1 class="contact__name">Daniel Moreau</h1>
      <p class="contact__title">Managing Director</p>
      <ul class="contact__list">
        <li><svg viewBox="0 0 24 24"><path d="M6.6 10.8a15 15 0 0 0 6.6 6.6l2.2-2.2c.3-.3.7-.4 1-.2 1.1.4 2.3.6 3.6.6.6 0 1 .4 1 1V20c0 .6-.4 1-1 1A17 17 0 0 1 3 4c0-.6.4-1 1-1h3.5c.6 0 1 .4 1 1 0 1.3.2 2.5.6 3.6.1.3 0 .7-.2 1z"/></svg>877-555-0142</li>
        <li><svg viewBox="0 0 24 24"><path d="M7 1h10a2 2 0 0 1 2 2v18a2 2 0 0 1-2 2H7a2 2 0 0 1-2-2V3a2 2 0 0 1 2-2zm0 3v15h10V4z"/></svg>877-555-0142</li>
        <li><svg viewBox="0 0 24 24"><path d="M2 5h20v14H2zm2 2v.5l8 5 8-5V7z"/></svg>info@stonebaybuild.com</li>
        <li><svg viewBox="0 0 24 24"><circle cx="12" cy="12" r="10"/></svg>www.stonebaybuild.com</li>
      </ul>
      <div class="social" aria-label="Social profiles"><span></span><span></span></div>
    </div>
  </section>

</main>
</body>
</html>
```